We need a business card for our gym. We are a PowerCore affiliate in Decatur Georgie established 2008. Our company name is Rally Functional Fitness. PowerCore Building Prime Fitness. Instagram and website is @rallygym. Hashtags we use #rallywithheart #madetorally We want something similar to the the black and neon green design attached but a different color scheme. No neon colors. Are company colors are the same as the blue and white card attached. We are open to ideas as far as colors however - just no neon.

Contact Information for Business Card

Rally Functional Fitness
472 Halvern Drive
Decatur GA 30041
Phone 404.555.0187 Website www.rallygym.example

Font styles to use
Other font styles liked:
• Futura Extra Bold Condensed

Colors

Designer to choose colors to be used in the design.

Requirements
Must have
• Our primary font we typically use for our name is Futura Extra Bold Condensed
Nice to have
• I attached a card from that is black and neon green from Zorva that we would like something similar. The blue and white is more similar to our colors. We also use have used black and white in the past. We use the chevrons as out logo. We are a PowerCore affiliate so I included a logo from them as well that may or may not be used on the card. Our instagram is @rallygym hashtags #madetorally #rallywithheart
Should not have
• No neon colors

```html
<!DOCTYPE html>
<html lang="en">
<head>
<meta charset="utf-8">
<title>Rally Functional Fitness – Business Card</title>
<link rel="stylesheet" href="https://fonts.googleapis.com/css2?family=Lato:wght@400;700;900&display=swap">
<style>
  :root {
    --bg: #2b2b2c;
    --card-front: #1e1f20;
    --card-back: #161717;
    --pattern-a: #1b1c1c;
    --pattern-b: #222323;
    --ink: #ffffff;
    --ink-soft: #e6e6e6;
    --rule: #5a5b5c;
  }
  * { box-sizing: border-box; margin: 0; padding: 0; }
  html, body {
    width: 1200px; height: 1108px; overflow: hidden;
    background: var(--bg);
    font-family: "Lato", Arial, sans-serif;
  }
  .stage {
    position: relative; width: 1200px; height: 1108px;
    display: flex; justify-content: center; align-items: center; gap: 60px;
  }
  .card {
    width: 400px; height: 660px; border-radius: 22px;
    position: relative; overflow: hidden;
  }
  .card--front { background: var(--card-front); color: var(--ink); }
  .card--back { background: var(--card-back); }

  .brand {
    position: absolute; top: 150px; left: 0; right: 0;
    display: flex; align-items: center; justify-content: center; gap: 14px;
  }
  .brand__sketch {
    width: 46px; height: 46px;
    background: linear-gradient(135deg, #3a3b3c, #262728);
  }
  .brand__mark { width: 16px; height: 16px; background: var(--ink); }
  .brand__name {
    font-weight: 900; font-size: 22px; letter-spacing: 1px;
    color: var(--ink); text-transform: uppercase;
  }

  .details {
    position: absolute; top: 330px; left: 0; right: 0;
    text-align: center; line-height: 1.2;
  }
  .person__name { font-weight: 900; font-size: 22px; letter-spacing: 0.5px; }
  .person__role { font-size: 18px; color: var(--ink-soft); }
  .rule { width: 170px; height: 1px; background: var(--rule); margin: 14px auto; }
  .contact { font-size: 18px; color: var(--ink-soft); }
  .label { font-weight: 700; color: var(--ink); }
  .address__co { font-weight: 700; font-size: 17px; }
  .address__line { font-size: 18px; color: var(--ink-soft); }

  .back__pattern {
    position: absolute; inset: 0;
    background:
      repeating-linear-gradient(135deg, var(--pattern-a) 0 22px, var(--pattern-b) 22px 44px);
  }
  .back__brand {
    position: absolute; left: 0; right: 0; bottom: 150px;
    display: flex; align-items: center; justify-content: center; gap: 10px;
  }
</style>
</head>
<body>
  <main class="stage">
    <section class="card card--front" aria-label="Card front">
      <div class="brand">
        <div class="brand__sketch" role="img" aria-label="Fine-line geometric sketch graphic"></div>
        <span class="brand__mark"></span>
        <span class="brand__name">Rally Functional Fitness</span>
      </div>
      <div class="details">
        <p class="person__name">MARCUS DELANE</p>
        <p class="person__role">Managing Director</p>
        <div class="rule"></div>
        <p class="contact">404.555.0187</p>
        <p class="contact">www.rallygym.example</p>
        <div class="rule"></div>
        <p class="contact"><span class="label">INSTAGRAM:</span> @rallygym</p>
        <div class="rule"></div>
        <p class="address__co">RALLY FUNCTIONAL FITNESS</p>
        <p class="address__line">472 Halvern Drive</p>
        <p class="address__line">Decatur GA 30041</p>
      </div>
    </section>

    <section class="card card--back" aria-label="Card back">
      <div class="back__pattern" role="img" aria-label="Tone-on-tone repeating brand pattern"></div>
      <div class="back__brand">
        <span class="brand__mark"></span>
        <span class="brand__name">Rally</span>
      </div>
    </section>
  </main>
</body>
</html>
```